KRT Engineering Business Card Design

We’re looking for an elegant, clean, and timeless business card design that communicates experience, capability, and reliability.

KRT Engineering was established in 1995 , we are a Government Contracting company providing Professional Services to the Office of Frontier Affairs, Harbor Protection and the Vantage Collective. Our capabilities include: Acquisition & Program Management; Intelligence & Security Operations; Cyber, IT & Network Operations; Lifecycle Logistics & Asset Readiness; C5ISR Systems Engineering & Sustainment.

We want the card to reflect a straightforward, confident approach to business. The design should feel polished and professional without being flashy or overly corporate.

Design Direction
Clean, sophisticated, and uncluttered
Elegant but understated
Strong typography and thoughtful spacing
A timeless aesthetic rather than something overly trendy
Confident and established, with a sense of substance
Easy to read and practical in a real-world business setting

The overall impression should be: “These are experienced professionals who know what they’re doing, do what they say, and can be relied upon.”

We’re open to creative interpretations. The finished card should feel distinctive through its typography, proportions, layout, and attention to detail rather than through excessive graphics or visual effects.

We’re looking for a design that would make a potential client immediately feel that they’re dealing with a capable, trustworthy, and established company.

Company Colors: Navy and Gold/Yellow (but you do not need to use these colors on the card)
Company Name: KRT Engineering Associates, Inc. (known as KRT Engineering)
Website: krtengineering.com
Company Logo: Navy & Gold (other variations attached)

```html
<!DOCTYPE html>
<html lang="en">
<head>
<meta charset="utf-8">
<title>KRT Engineering Business Card</title>
<link rel="stylesheet" href="https://fonts.googleapis.com/css2?family=Poppins:ital,wght@0,400;0,500;0,600;0,700;0,800;1,400&display=swap">
<style>
  :root {
    --navy: #1b2640;
    --navy-ink: #1f2a63;
    --gold: #f5d43c;
    --gold-line: #f0c63a;
    --ink: #2b2b2b;
    --rule: #dcdcdc;
    --backdrop: #c3c3c3;
    --paper: #ffffff;
  }
  * { margin: 0; padding: 0; box-sizing: border-box; }
  html, body { width: 1036px; height: 1200px; overflow: hidden; }
  body { background: var(--backdrop); font-family: "Poppins", sans-serif; position: relative; }
  .card { position: absolute; left: 117px; width: 802px; height: 458px; }
  .card-front { top: 112px; background: var(--navy); color: #fff; }
  .card-back { top: 630px; background: var(--paper); color: var(--ink); }
  .abs { position: absolute; line-height: 1; white-space: nowrap; }

  /* front */
  .front-wordmark { left: 0; right: 0; top: 116px; text-align: center; font-weight: 800; font-size: 104px; letter-spacing: -2px; color: #fff; }
  .front-company { left: 0; right: 0; top: 240px; text-align: center; font-size: 15.5px; font-weight: 500; letter-spacing: 0.36em; padding-left: 0.36em; }
  .front-divider { left: 192px; top: 279px; width: 418px; height: 14px; }
  .front-established { left: 0; right: 0; top: 318px; text-align: center; font-size: 14px; font-weight: 500; letter-spacing: 0.36em; padding-left: 0.36em; }
  .front-tagline { left: 0; right: 0; top: 375px; text-align: center; font-size: 13.5px; font-weight: 500; color: var(--gold); letter-spacing: 0.17em; }

  /* back: contact */
  .back-wordmark { left: 105px; top: 76px; font-weight: 800; font-size: 36px; color: var(--navy-ink); letter-spacing: -0.5px; }
  .person-name { left: 84px; top: 130px; font-weight: 700; font-size: 21px; color: var(--navy-ink); }
  .person-title { left: 83px; top: 156px; font-style: italic; font-size: 13.5px; }
  .contact-rule { left: 83px; top: 192px; width: 261px; height: 1px; background: var(--gold-line); }
  .contact-company { left: 83px; top: 206px; font-size: 15px; }
  .contact-list { position: absolute; left: 83px; top: 240px; list-style: none; }
  .contact-item { position: absolute; left: 0; display: flex; gap: 10px; font-size: 14.5px; line-height: 17.5px; white-space: nowrap; }
  .contact-item svg { width: 18px; height: 18px; flex: none; }
  .column-rule { left: 376px; top: 59px; width: 1px; height: 286px; background: var(--gold-line); }

  /* back: capabilities */
  .cap-heading { left: 408px; top: 71px; font-size: 13.5px; font-weight: 500; letter-spacing: 0.3em; }
  .cap-heading-rule { left: 408px; top: 107px; width: 303px; height: 1px; background: var(--gold-line); }
  .cap-list { position: absolute; left: 408px; top: 110px; width: 313px; list-style: none; }
  .cap-item { display: flex; align-items: center; height: 42px; border-bottom: 1px solid var(--rule); font-size: 14.5px; line-height: 17px; }
  .cap-item:last-child { border-bottom: none; height: 50px; }
  .cap-item svg { width: 30px; height: 30px; margin-right: 16px; flex: none; }
  .footer-rule { left: 48px; top: 366px; width: 707px; height: 1px; background: var(--gold-line); }
  .values { left: 0; right: 0; top: 386px; display: flex; justify-content: center; align-items: center; gap: 16px; font-size: 14px; font-weight: 500; letter-spacing: 0.2em; }
  .values svg { width: 12px; height: 12px; }
</style>
</head>
<body>

<section class="card card-front" aria-label="Card front">
  <div class="abs front-wordmark">KRT</div>
  <div class="abs front-company">KRT ENGINEERING ASSOCIATES, INC.</div>
  <svg class="abs front-divider" viewBox="0 0 418 14" aria-hidden="true">
    <line x1="0" y1="7" x2="200" y2="7" stroke="var(--gold)" stroke-width="1"/>
    <line x1="218" y1="7" x2="418" y2="7" stroke="var(--gold)" stroke-width="1"/>
    <polygon points="209,1 210.8,5.2 215,5.4 211.8,8.2 212.8,12.5 209,10.2 205.2,12.5 206.2,8.2 203,5.4 207.2,5.2" fill="var(--gold)"/>
  </svg>
  <div class="abs front-established">ESTABLISHED 1995</div>
  <div class="abs front-tagline">Professional Services for Defense, Security &amp; Intelligence</div>
</section>

<section class="card card-back" aria-label="Card back">
  <div class="abs back-wordmark">KRT</div>
  <div class="abs person-name">Marian Holloway</div>
  <div class="abs person-title">President, CEO, &amp; Founder</div>
  <div class="abs contact-rule"></div>
  <div class="abs contact-company">KRT Engineering Associates, Inc.</div>
  <ul class="contact-list">
    <li class="contact-item" style="top:0">
      <svg viewBox="0 0 24 24" fill="none" stroke="var(--gold-line)" stroke-width="2" stroke-linecap="round" stroke-linejoin="round"><path d="M5 3h4l2 5-2.5 1.5a11 11 0 0 0 6 6L16 13l5 2v4a2 2 0 0 1-2 2A16 16 0 0 1 3 5a2 2 0 0 1 2-2"/><path d="M15 3a6 6 0 0 1 6 6M15 7a2 2 0 0 1 2 2"/></svg>
      <span>555-013-0142</span>
    </li>
    <li class="contact-item" style="top:30px">
      <svg viewBox="0 0 24 24" fill="none" stroke="var(--gold-line)" stroke-width="2" stroke-linecap="round"><path d="M12 21s-6-6-6-11a6 6 0 0 1 12 0c0 5-6 11-6 11z"/><circle cx="12" cy="10" r="2.2"/></svg>
      <span>4200 Harborline Avenue, Suite 310,<br>Coastview, VA 23000</span>
    </li>
    <li class="contact-item" style="top:82px">
      <svg viewBox="0 0 24 24" fill="none" stroke="var(--gold-line)" stroke-width="2"><circle cx="12" cy="12" r="9"/><path d="M3 12h18M12 3c3 3 3 15 0 18M12 3c-3 3-3 15 0 18"/></svg>
      <span>krtengineering.com</span>
    </li>
  </ul>
  <div class="abs column-rule"></div>

  <div class="abs cap-heading">CAPABILITIES</div>
  <div class="abs cap-heading-rule"></div>
  <ul class="cap-list">
    <li class="cap-item">
      <svg viewBox="0 0 30 30" fill="none" stroke="var(--gold-line)" stroke-width="1.2"><circle cx="15" cy="7" r="4"/><circle cx="15" cy="7" r="1.5"/><path d="M3 20l5-4 5 2 4-2 5 2 5 2M6 22l4 3 5-2 4 2 5-3"/></svg>
      <span>Acquisition &amp; Program Management</span>
    </li>
    <li class="cap-item">
      <svg viewBox="0 0 30 30" fill="none" stroke="var(--gold-line)" stroke-width="1.2"><circle cx="17" cy="12" r="6"/><circle cx="17" cy="12" r="2.5"/><path d="M4 14l5-2 5 2v5c0 4-5 6-5 6s-5-2-5-6z"/></svg>
      <span>Intelligence &amp; Security Operations</span>
    </li>
    <li class="cap-item">
      <svg viewBox="0 0 30 30" fill="none" stroke="var(--gold-line)" stroke-width="1.2"><circle cx="15" cy="15" r="8"/><rect x="11.5" y="14" width="7" height="6" rx="1"/><path d="M13 14v-2a2 2 0 0 1 4 0v2M3 15h4M23 15h4M15 3v4M15 23v4"/></svg>
      <span>Cyber, IT &amp; Network Operations</span>
    </li>
    <li class="cap-item">
      <svg viewBox="0 0 30 30" fill="none" stroke="var(--gold-line)" stroke-width="1.2"><circle cx="15" cy="15" r="11"/><circle cx="15" cy="15" r="6"/><circle cx="15" cy="15" r="2.5"/></svg>
      <span>Lifecycle Logistics &amp; Asset Readiness</span>
    </li>
    <li class="cap-item">
      <svg viewBox="0 0 30 30" fill="none" stroke="var(--gold-line)" stroke-width="1.2"><path d="M6 10a11 11 0 0 1 18 0M24 20a11 11 0 0 1-18 0"/><circle cx="15" cy="15" r="5"/><circle cx="15" cy="15" r="2"/><path d="M24 6v4h-4M6 24v-4h4"/></svg>
      <span>C5ISR Systems Engineering<br>&amp; Sustainment</span>
    </li>
  </ul>

  <div class="abs footer-rule"></div>
  <div class="abs values">
    <span>INTEGRITY</span>
    <svg viewBox="0 0 12 12" aria-hidden="true"><polygon points="6,0 7.5,4.2 12,4.4 8.4,7.1 9.7,11.6 6,9 2.3,11.6 3.6,7.1 0,4.4 4.5,4.2" fill="var(--gold-line)"/></svg>
    <span>EXCELLENCE</span>
    <svg viewBox="0 0 12 12" aria-hidden="true"><polygon points="6,0 7.5,4.2 12,4.4 8.4,7.1 9.7,11.6 6,9 2.3,11.6 3.6,7.1 0,4.4 4.5,4.2" fill="var(--gold-line)"/></svg>
    <span>MISSION FOCUSED</span>
  </div>
</section>

</body>
</html>
```